BOLD & MINIMALIST DESIGN NEEDED

We want a very bold but minimalistic business card design that is impactful and utilizes both sides of the business card. Our current logo is included for your use.

We want bold fonts and good use of negative space. We don't want the logo to overpower the design.

Target Market(s)

Professionals who are building new commercial buildings.

Industry/Entity Type

Construction

Contact Information for Business Card

Name, Title, email, office phone, cell phone, website

Font styles to use
Serif
Sans Serif

Requirements
Must have
• Bold design!

```html
<!DOCTYPE html>
<html lang="en">
<head>
<meta charset="utf-8">
<title>Ridgeline Build – Business Card</title>
<link rel="stylesheet" href="https://fonts.googleapis.com/css2?family=Poppins:wght@300;400;700&family=Ubuntu:wght@700&display=swap">
<style>
  :root {
    --backdrop: #ababab;
    --paper: #ffffff;
    --ink: #0b0c0e;
    --green: #84c42a;
    --white: #ffffff;
  }
  * { margin: 0; padding: 0; box-sizing: border-box; }
  html, body {
    width: 1093px; height: 1200px; overflow: hidden;
    background: var(--backdrop);
  }
  body { position: relative; font-family: "Poppins", sans-serif; }

  .card {
    position: absolute; left: 264px;
    width: 579px; height: 357px;
    background: var(--paper); overflow: hidden;
  }
  .card--front { top: 226px; }
  .card--back { top: 620px; }
  .card__art { position: absolute; inset: 0; }

  .band { position: absolute; left: 0; background: var(--ink); }
  .card--front .band { top: 271px; width: 579px; height: 47px; }
  .card--back .band { top: 259px; width: 250px; height: 55px; }

  .accent {
    position: absolute; background: var(--green);
  }
  .card--front .accent--one { left: 44px; top: 258px; width: 84px; height: 82px; }
  .card--front .accent--two { left: 146px; top: 258px; width: 84px; height: 82px; }
  .card--back .accent { left: 118px; top: 243px; width: 84px; height: 82px; }

  .wordmark {
    position: absolute; display: flex; align-items: center; gap: 12px;
    font-family: "Poppins", sans-serif; font-weight: 700;
    color: var(--ink); letter-spacing: 1px; white-space: nowrap;
  }
  .wordmark__square { display: block; background: var(--green); }
  .card--front .wordmark { left: 0; right: 0; top: 100px; justify-content: center; font-size: 40px; }
  .card--front .wordmark__square { width: 24px; height: 24px; }
  .card--back .wordmark { left: 28px; top: 104px; font-size: 25px; }
  .card--back .wordmark__square { width: 18px; height: 18px; }

  .front__url {
    position: absolute; right: 45px; top: 282px;
    color: var(--white); font-size: 17px; font-weight: 400; letter-spacing: .3px;
  }

  .panel { position: absolute; inset: 0; }

  .person {
    position: absolute; right: 26px; top: 148px; text-align: right;
  }
  .person__name {
    font-family: "Ubuntu", sans-serif; font-weight: 700;
    color: var(--white); font-size: 22px; letter-spacing: .5px; line-height: 1.2;
  }
  .person__title {
    color: var(--green); font-size: 14px; font-weight: 300; margin-top: 2px; letter-spacing: .3px;
  }
  .person__rule {
    position: absolute; left: 367px; top: 208px; width: 186px; height: 1px; background: var(--green);
  }
  .contacts {
    position: absolute; right: 26px; top: 240px; list-style: none;
  }
  .contacts li {
    display: flex; justify-content: flex-end; align-items: center; gap: 7px;
    color: var(--white); font-size: 16px; font-weight: 300; line-height: 21px; letter-spacing: .3px;
  }
  .contacts svg { width: 15px; height: 15px; flex: none; }
</style>
</head>
<body>

<section class="card card--front" aria-label="Business card front">
  <div class="band"></div>
  <div class="accent accent--one" role="img" aria-label="Green ribbon accent crossing the band"></div>
  <div class="accent accent--two" role="img" aria-label="Green ribbon accent crossing the band"></div>
  <div class="wordmark"><span class="wordmark__square"></span>RIDGELINE BUILD</div>
  <p class="front__url">www.ridgelinebuild.com</p>
</section>

<section class="card card--back" aria-label="Business card back">
  <svg class="panel" viewBox="0 0 579 357" aria-hidden="true">
    <polygon points="396,0 579,0 579,357 188,357" fill="var(--ink)"/>
  </svg>
  <div class="band"></div>
  <div class="accent" role="img" aria-label="Green ribbon accent crossing the band"></div>

  <div class="wordmark"><span class="wordmark__square"></span>RIDGELINE BUILD</div>

  <div class="person">
    <p class="person__name">DANIEL HARTLEY</p>
    <p class="person__title">MANAGING DIRECTOR</p>
  </div>
  <span class="person__rule"></span>

  <ul class="contacts">
    <li>021-555 0147
      <svg viewBox="0 0 16 16" aria-label="Office phone"><path d="M3 1.5l2.5 0 1 3.2-1.6 1.2a8 8 0 0 0 5.2 5.2l1.2-1.6 3.2 1V13a1.6 1.6 0 0 1-1.7 1.5A12 12 0 0 1 1.5 3.2 1.6 1.6 0 0 1 3 1.5z" fill="none" stroke="var(--green)" stroke-width="1.5"/><path d="M9.5 1.5a5 5 0 0 1 5 5M9.5 4a2.5 2.5 0 0 1 2.5 2.5" fill="none" stroke="var(--green)" stroke-width="1.3"/></svg>
    </li>
    <li>021-555 0147
      <svg viewBox="0 0 16 16" aria-label="Mobile phone"><rect x="3.5" y="1" width="9" height="14" rx="1.5" fill="none" stroke="var(--green)" stroke-width="1.5"/><line x1="6.5" y1="2.8" x2="9.5" y2="2.8" stroke="var(--green)" stroke-width="1"/><circle cx="8" cy="12.8" r=".9" fill="var(--green)"/></svg>
    </li>
    <li>hello@ridgelinebuild.com
      <svg viewBox="0 0 16 16" aria-label="Email"><rect x="1" y="4" width="14" height="9" fill="var(--green)"/><path d="M1 4l7 5 7-5M1 13l5-4.5M15 13l-5-4.5" fill="none" stroke="var(--ink)" stroke-width="1"/></svg>
    </li>
    <li>www.ridgelinebuild.com
      <svg viewBox="0 0 16 16" aria-label="Website"><circle cx="8" cy="8" r="6.5" fill="none" stroke="var(--green)" stroke-width="1.5"/><ellipse cx="8" cy="8" rx="2.8" ry="6.5" fill="none" stroke="var(--green)" stroke-width="1.2"/><path d="M1.5 8h13M2.8 4.8h10.4M2.8 11.2h10.4" stroke="var(--green)" stroke-width="1.1"/></svg>
    </li>
  </ul>
</section>

</body>
</html>
```